Cruise Booking Website

Cruise search and booking website

This project is a redesign of a cruise booking website we did a few years ago.

The current website is located here: http://voyage.pylonworks.example/en/

It's not fully functional but gives you ad idea how miserable the old design was.

All the information about cruises, cruise lines, destinations, ports and shore excursions will be similar to http://www.sailquest.example/
Actual search pages (form, results, single result, sailing and cabin selection, ship info, booking) will have EXACTLY the same info as sailquest.example

We like the style of http://harborfleetdesk.example, it's quite modern, good spacing, not overloaded with information. So you can use it as an example of what we like, not what we want as a final result for us. Please, don't copy it. The result should not be possible to resemble the harborfleetdesk.example, because our site has to be unique. This is important!
If you submit a design that clearly reminds another cruise site it will be rejected!

Also the mockup provided is just to give you the basic structure and show what information has to be present on the page. It doesn't mean the layout has to be the same as a mockup. The layout is up to the designer.

I've updated the mockup to be more generic so it doesn't confuse you:
https://files.boxvault.example/s/k7m2qp9wz4hx/Home%20page.png

When you're adding social sharing icons like plazanet/chirpline you have to use chinese ones instead:
https://files.boxvault.example/s/t3nr8vx5lc2e/chinese-social-icons.png
Originals: http://minilk.example/qR7t

We'll start with home page first and after it's approved inner pages can be designed.

I know the cost of the project doesn't look high, but the task is straight forward and doesn't require to be very original, it's better to follow existing design and layout patterns that proved to work well.
That's why I encourage you to choose a template to build the design on top of one of https://themeparlor.example/ themes if it will save the design work, will be easier and faster for you. So it will be more like a customization than a new design from scratch.

Mockups, site map and logo files:
- https://files.boxvault.example/sh/h48dm2rs73fkpw/QvnbW2Xz8e

Website tree:
- https://sheets.papernest.example/document/d/7xPqR2mLw9sTk4VbN8cHj3YzA6eUf5GdKo1iMnBv/edit?usp=sharing
Updates

So far a lot of designs are just copying http://www.harborfleetdesk.example/ - we don't like it!

We like the style of harborfleetdesk.example, it's quite modern, good spacing, not overloaded with information. So you can use it as an example of what we like, not what we want as a final result for us. Please, don't copy it. The result should not be possible to resemble the harborfleetdesk.example, because our site has to be unique. This is important!

Target Market(s)

Chinese travellers

Industry/Entity Type

Build

Requirements
Must have
• * White, blue and red
* Large spacing, not too much information cramped into a small space like sailquest.example or the current website
* More "hidden" info in popups, tabs and so on, so not to many things are visible at the same time
* Compatible with kestrel scaffold styling (for easier coding):
- http://kestrelkit.codeshelf.example/scaffold/index.html
- http://skinmarket.example/
* Feel free to propose to build the design on top of one of https://themeparlor.example/ themes if it will save the design work, will be easier and faster for you

```html
<!DOCTYPE html>
<html lang="en">
<head>
<meta charset="utf-8">
<title>Oceanwake – Cruise Booking</title>
<link rel="stylesheet" href="https://fonts.googleapis.com/css2?family=Source+Sans+3:ital,wght@0,400;0,600;0,700;1,700&display=swap">
<style>
:root{
  --bg-deep:#1d5f9a;
  --bg-light:#6fa6d6;
  --blue:#1f6aa8;
  --blue-dark:#185a93;
  --nav:#1b72b8;
  --nav-active:#2a9be0;
  --text:#3a3a3a;
  --muted:#777;
  --orange:#f58a12;
  --orange-dark:#e46a00;
  --panel:#2a2a2a;
  --footer:#3f77aa;
  --footer-bar:#356a9c;
  --line:#dcdcdc;
  --tab:#6a6a6a;
  --tick:#5aac1e;
}
*{box-sizing:border-box;margin:0;padding:0}
html,body{width:1161px;height:1200px;overflow:hidden}
body{font-family:"Source Sans 3",sans-serif;color:var(--text);
  background:radial-gradient(ellipse at 50% 45%,var(--bg-light) 0%,#3e7fba 45%,var(--bg-deep) 100%);position:relative}
.page{position:absolute;left:174px;top:0;width:813px;height:1200px;background:#fff}
.abs{position:absolute}
/* header */
.logo{left:12px;top:34px;display:flex;align-items:center;gap:8px}
.logo-mark{width:40px;height:40px;border-radius:50%;background:var(--blue)}
.logo-name{font-size:32px;font-weight:700;color:var(--blue);letter-spacing:.5px}
.account{left:595px;top:16px;font-size:11px;color:var(--blue)}
.account span{margin:0 6px;color:var(--muted)}
.social{left:700px;top:13px;display:flex;gap:4px}
.social i{width:21px;height:21px;border-radius:3px;display:block}
.search{left:431px;top:64px;width:191px;height:21px;border:1px solid #cfcfcf;border-radius:2px;background:#f6f6f6;font-size:8px;color:#888;padding:5px 8px}
.search svg{position:absolute;right:6px;top:4px}
.callbox{left:638px;top:47px;width:158px;height:53px;border:1px solid var(--line);padding:6px 8px 0 46px}
.callbox svg{position:absolute;left:8px;top:12px}
.callbox b{display:block;font-size:18px;color:var(--blue);font-weight:700;line-height:20px}
.callbox em{font-style:normal;font-size:15px;color:#444}
/* nav */
.nav{left:0;top:108px;width:813px;height:33px;background:linear-gradient(var(--nav),#1566a8);display:flex}
.nav a{color:#fff;font-size:10px;font-weight:700;text-decoration:none;display:flex;align-items:center;justify-content:center;border-right:1px solid rgba(255,255,255,.15)}
.nav a.on{background:var(--nav-active)}
/* hero */
.hero{left:0;top:141px;width:813px;height:414px;background:linear-gradient(110deg,#c9b9a4 0%,#a68a74 35%,#d14d7f 50%,#9c8c7c 70%,#6b7a70 100%)}
.tagline{left:344px;top:210px;color:#fff;font-style:italic;font-weight:700;text-shadow:0 1px 3px rgba(0,0,0,.4)}
.tagline .t1{font-size:20px;letter-spacing:-.5px}
.tagline .t2{font-size:28px;letter-spacing:-1px;line-height:30px}
.dots{left:750px;top:387px;display:flex;gap:4px}
.dots i{width:9px;height:9px;border-radius:50%;background:#fff;opacity:.85}
.finder{left:558px;top:36px;width:238px;height:337px;background:rgba(34,34,34,.93);border-radius:3px;color:#eee;padding:0 18px}
.finder h2{font-weight:400;font-size:21px;color:#fff;padding:16px 3px 6px;border-bottom:1px solid #444;margin:0 -18px 0;padding-left:21px}
.finder label{display:block;font-size:11px;margin-top:8px;margin-bottom:3px}
.sel{height:22px;background:linear-gradient(#f4f4f4,#d8d8d8);border-radius:2px;font-size:8.5px;color:#333;padding:5px 9px;position:relative}
.sel::after{content:"";position:absolute;right:0;top:0;width:18px;height:22px;border-left:1px solid #bbb;background:linear-gradient(#eee,#ccc)}
.sel s{position:absolute;right:5px;top:5px;z-index:1;text-decoration:none;font-size:6px;line-height:5px;color:#666}
.row{display:flex;gap:19px}
.row>div{flex:1}
.finder h3{font-weight:400;font-size:13px;margin-top:12px}
.check{font-size:9px;margin-top:8px;display:flex;align-items:center;gap:4px}
.check i{width:11px;height:11px;background:#ddd;border-radius:2px}
.btn-search{margin-top:11px;height:32px;border-radius:2px;background:linear-gradient(#ffa42a,var(--orange-dark));color:#fff;font-size:14px;font-weight:600;display:flex;align-items:center;justify-content:center;border:1px solid #ffb957}
/* tabs */
.tabs{left:13px;top:575px;display:flex;height:30px}
.tab{height:30px;padding:0 25px 0 20px;background:var(--tab);color:#ddd;font-size:11px;display:flex;align-items:center;clip-path:polygon(0 0,88% 0,100% 100%,0 100%);margin-right:-4px}
.tab.on{background:#8fd0f0;background:linear-gradient(#9cd7f4,#62b7e4);color:#1f5f91}
.tabbox{left:13px;top:605px;width:585px;height:250px;border:1px solid var(--line)}
.ph{background:linear-gradient(#a9cdec 0%,#2a9ac7 40%,#1488b5 100%);border:3px solid #d8d8d8}
.pitch{left:364px;top:632px;width:225px}
.pitch h2{font-size:23px;font-weight:700;color:var(--blue);letter-spacing:.2px}
.pitch .easy{font-size:15px;color:#444;margin-top:2px}
.pitch .lead{font-size:15px;color:var(--blue);line-height:18px;margin-top:9px}
.ticks{list-style:none;margin-top:14px}
.ticks li{font-size:8.5px;color:#444;display:flex;align-items:center;gap:6px;height:22px}
/* newsletter */
.news{left:627px;top:570px;width:178px;height:285px;border:1px solid var(--line);padding:12px 12px 0}
.news .ph2{height:131px;background:linear-gradient(#8fb4d6 0%,#36628a 55%,#173a5c 100%)}
.news h4{font-size:12px;color:var(--blue);margin-top:13px;font-weight:700}
.news p{font-size:12px;color:var(--blue);line-height:18px}
.email{margin-top:8px;height:22px;border:1px solid #ccc;border-radius:2px;font-size:9px;color:#888;padding:4px 9px;background:#f8f8f8}
.sub{margin-top:11px;width:84px;height:22px;border-radius:2px;background:linear-gradient(#ff8a1c,#e8560a);color:#fff;font-size:10px;display:flex;align-items:center;justify-content:center}
/* partners */
.partners-h{left:15px;top:880px;font-size:15px;font-weight:700;color:var(--blue)}
.arrows{left:759px;top:882px;display:flex;gap:3px}
.arrows i{width:16px;height:16px;background:#ddd;display:flex;align-items:center;justify-content:center}
.partners{left:16px;top:911px;display:flex;gap:13px}
.partner{width:120px;height:60px;border:1px solid var(--line);display:flex;align-items:center;justify-content:center}
.partner i{width:70px;height:16px;border-radius:3px;display:block}
/* footer */
.footer{left:0;top:974px;width:813px;height:184px;background:var(--footer);color:#fff}
.fcol{position:absolute;top:24px}
.fcol h5{font-size:13px;font-weight:700;margin-bottom:7px}
.fcol a{display:block;font-size:8.5px;color:#fff;text-decoration:none;line-height:18.2px}
.about-badge{width:82px;height:80px;background:#fff;margin-top:10px;display:flex;align-items:center;justify-content:center}
.about-badge i{width:38px;height:38px;border-radius:50%;background:var(--blue)}
.about-text{position:absolute;left:98px;top:35px;width:95px;font-size:10px;line-height:15px}
.contact p{font-size:10.5px;line-height:16px}
.contact .ln{display:flex;align-items:center;gap:6px;font-size:10px;margin-top:7px}
.bar{left:0;top:1158px;width:813px;height:42px;background:var(--footer-bar);color:#fff;font-size:8.5px;display:flex;align-items:center;justify-content:center}
</style>
</head>
<body>
<div class="page">
  <header>
    <div class="abs logo"><i class="logo-mark"></i><span class="logo-name">Oceanwake</span></div>
    <div class="abs account">Sign in<span>|</span>Signup</div>
    <div class="abs social" aria-label="Social links">
      <i style="background:#e2322c"></i><i style="background:#2aa2dc"></i><i style="background:#f0a81c"></i><i style="background:#e64a3c"></i>
    </div>
    <div class="abs search">SEARCH :
      <svg width="11" height="11" viewBox="0 0 11 11"><circle cx="4.5" cy="4.5" r="3.5" fill="none" stroke="#bbb" stroke-width="1.3"/><path d="M7 7l3 3" stroke="#bbb" stroke-width="1.4"/></svg>
    </div>
    <div class="abs callbox">
      <svg width="30" height="30" viewBox="0 0 30 30"><circle cx="15" cy="15" r="14" fill="none" stroke="#999" stroke-width="1.2"/><path d="M11 8c-2 1-2 4 0 8s5 7 8 7c1 0 2-1 2-2l-3-3-2 1c-1-1-3-3-4-5l1-2-2-4z" fill="#888"/></svg>
      <b>400 818 302</b><em>Call Us Today!</em>
    </div>
  </header>

  <nav class="abs nav">
    <a class="on" style="width:84px">HOME</a>
    <a style="width:117px">DESTINATIONS</a>
    <a style="width:107px">CRUISE LINES</a>
    <a style="width:106px">CRUISE INFO</a>
    <a style="width:79px">DEALS</a>
    <a style="width:127px">ONLINE BOOKING</a>
    <a style="width:103px">CONTACT US</a>
    <a style="width:90px;border:0">BLOG</a>
  </nav>

  <section class="abs hero" role="img" aria-label="Photo of a smiling couple embracing in a sunny old-town square">
    <div class="abs tagline"><div class="t1">Cruise Vacations</div><div class="t2">&amp; So much more...</div></div>
    <div class="abs dots"><i></i><i></i><i></i></div>
    <form class="abs finder">
      <h2>Find Your Cruise</h2>
      <label>Destination</label>
      <div class="sel">Destination name<s>▲<br>▼</s></div>
      <div class="row">
        <div><label>Length</label><div class="sel">Length Area</div></div>
        <div><label>Month</label><div class="sel"><s>▲<br>▼</s></div></div>
      </div>
      <label>Cruise Lines</label>
      <div class="sel">Any Cruise line<s>▲<br>▼</s></div>
      <h3>Number of Travelers</h3>
      <div class="row">
        <div><label>Age 25+</label><div class="sel">5<s>▲<br>▼</s></div></div>
        <div><label>Age 0 to 24</label><div class="sel">0<s>▲<br>▼</s></div></div>
      </div>
      <div class="check"><i></i>Check for senior rates</div>
      <div class="btn-search">Search Cruises</div>
    </form>
  </section>

  <div class="abs tabs">
    <div class="tab on">BOOK WITH US</div>
    <div class="tab">DEALS</div>
    <div class="tab">PACKAGES</div>
    <div class="tab">NEWS</div>
    <div class="tab">FIRST TIME CRUISER?</div>
  </div>
  <div class="abs tabbox"></div>
  <div class="abs ph" style="left:32px;top:631px;width:306px;height:195px" role="img" aria-label="Photo of a couple sitting on a sea wall looking out over turquoise water"></div>
  <div class="abs pitch">
    <h2>BOOK WITH US!</h2>
    <div class="easy">It's easy and Fun</div>
    <div class="lead">We're most advanced cruise booking provider in china</div>
    <ul class="ticks">
      <li><svg width="11" height="9" viewBox="0 0 11 9"><path d="M1 5l3 3 6-7" fill="none" stroke="var(--tick)" stroke-width="2"/></svg>Great prices</li>
      <li><svg width="11" height="9" viewBox="0 0 11 9"><path d="M1 5l3 3 6-7" fill="none" stroke="var(--tick)" stroke-width="2"/></svg>Fast booking processing</li>
      <li><svg width="11" height="9" viewBox="0 0 11 9"><path d="M1 5l3 3 6-7" fill="none" stroke="var(--tick)" stroke-width="2"/></svg>20 Cruise Lines</li>
      <li><svg width="11" height="9" viewBox="0 0 11 9"><path d="M1 5l3 3 6-7" fill="none" stroke="var(--tick)" stroke-width="2"/></svg>Destinations around the world</li>
    </ul>
  </div>

  <aside class="abs news">
    <div class="ph2" role="img" aria-label="Photo of a white cruise ship at sea"></div>
    <h4>Cruise Deals Newsletter</h4>
    <p>Subscribe to the best deals Now!</p>
    <div class="email">Email :</div>
    <div class="sub">Subscribe</div>
  </aside>

  <h3 class="abs partners-h">OUR RELIABLE PARTNERS</h3>
  <div class="abs arrows">
    <i><svg width="6" height="8"><path d="M5 0L1 4l4 4" fill="none" stroke="#888"/></svg></i>
    <i><svg width="6" height="8"><path d="M1 0l4 4-4 4" fill="none" stroke="#888"/></svg></i>
  </div>
  <div class="abs partners">
    <div class="partner"><i style="background:#c7392f"></i></div>
    <div class="partner"><i style="background:#1d5fae"></i></div>
    <div class="partner"><i style="background:#2d5a88"></i></div>
    <div class="partner"><i style="background:#f0a23a"></i></div>
    <div class="partner"><i style="background:#4aa9dc"></i></div>
    <div class="partner"><i style="background:#2e8fd4"></i></div>
  </div>

  <footer class="abs footer">
    <div class="fcol" style="left:27px">
      <h5>Useful Pages</h5>
      <a>About Us</a><a>Contact us</a><a>Blog</a><a>FAQ</a><a>Terms of Service</a><a>Payment info</a><a>Reward Points</a>
    </div>
    <div class="fcol" style="left:184px">
      <h5>Cruise Infov</h5>
      <a>Cruise news</a><a>Visa</a><a>Honeymoon cruises</a><a>Firsttime on a Cruise</a>
    </div>
    <div class="fcol" style="left:336px;top:29px">
      <h5>About oceanwake.example</h5>
      <div class="about-badge"><i></i></div>
      <div class="about-text">We're the most advanced cruise booking providr in china.</div>
    </div>
    <div class="fcol contact" style="left:585px;top:29px">
      <h5>Contact Us</h5>
      <p>Tidewell Studio Ltd<br>Harbourline Centre x118, Quay Ave 7<br>Portvale 20481 Coastland</p>
      <div class="ln"><svg width="12" height="10" viewBox="0 0 12 10"><path d="M1 3c0-2 10-2 10 0v1H8V3H4v1H1z M3 5h6l2 4H1z" fill="#fff"/></svg>(021) 310-4472 - (021)310-4473</div>
      <div class="ln"><svg width="12" height="9" viewBox="0 0 12 9"><rect x=".5" y=".5" width="11" height="8" fill="none" stroke="#fff"/><path d="M.5 .5l5.5 4.5 5.5-4.5" fill="none" stroke="#fff"/></svg>hello@oceanwake.example</div>
    </div>
  </footer>
  <div class="abs bar">© 2013. Oceanwake. All rights reserved.</div>
</div>
</body>
</html>
```